Telecommunications/Power civil contractor needs business card design

Were a new telecommunications/power underground civil contractor that is looking for a new business card design. Our company colours are silver or grey and orange. Feel free to use the white background logo or the black background logo.

Target Market(s)

Local contractors, utility companies, private sector mining/energy companies, developers.

Industry/Entity Type

Telecommunications

Contact Information for Business Card

Each card will need the following info:
Persons name:
Title:
E-mail:
Phone number:
Shop Address:
Mailing Address:

Requirements
Must have
• Each card will need the following info:
• Persons name:
• Title:
• E-mail:
• Phone number:
• Shop Address:
• Mailing Address:

```html
<!DOCTYPE html>
<html lang="en">
<head>
<meta charset="utf-8">
<title>Dig Line Contracting Inc – Business Card</title>
<link rel="stylesheet" href="https://fonts.googleapis.com/css2?family=Source+Sans+3:wght@400;600;700&display=swap">
<style>
  :root {
    --orange: #f15a24;
    --orange-dark: #e4501c;
    --grey: #77787b;
    --grey-dark: #5e5f62;
    --white: #ffffff;
    --backdrop: #ecebe9;
  }
  * { margin: 0; padding: 0; box-sizing: border-box; }
  html, body { width: 1200px; height: 900px; overflow: hidden; }
  body {
    position: relative;
    background: var(--backdrop);
    font-family: "Source Sans 3", "Segoe UI", Arial, sans-serif;
    color: var(--white);
  }

  .card { position: absolute; overflow: hidden; box-shadow: 0 6px 18px rgba(0,0,0,.18); }

  /* Front of card */
  .card-front { left: 78px; top: 34px; width: 588px; height: 363px; background: var(--white); }
  .card-front .bands { position: absolute; inset: 0; }

  .brand { position: absolute; display: flex; align-items: center; gap: 16px; }
  .brand-mark { border-radius: 50%; flex: none; }
  .brand-name { font-weight: 700; line-height: .95; text-transform: uppercase; letter-spacing: .5px; }
  .brand-name .line-main { display: block; font-size: 46px; }
  .brand-name .line-sub { display: block; font-size: 23px; letter-spacing: 1.4px; margin-top: 4px; }

  .card-front .brand { left: 90px; top: 43px; }
  .card-front .brand-mark { width: 100px; height: 100px; background: var(--orange); }
  .card-front .brand-name { color: var(--grey); }

  .contact { position: absolute; right: 305px; top: 207px; text-align: right; font-size: 16px; line-height: 23px; }
  .contact-row { display: flex; justify-content: flex-end; align-items: center; gap: 7px; }
  .contact-row svg { flex: none; }

  .address { position: absolute; font-size: 16px; line-height: 18px; }
  .address-title { font-size: 18.5px; font-weight: 600; line-height: 21px; }
  .address-mailing { right: 305px; top: 273px; text-align: right; }
  .address-shop { left: 312px; top: 272px; }

  .person { position: absolute; left: 312px; top: 203px; }
  .person-name { font-size: 23px; font-weight: 600; line-height: 28px; }
  .person-title { font-size: 16px; line-height: 20px; }

  /* Back of card */
  .card-back { left: 388px; top: 505px; width: 567px; height: 352px; background: var(--orange); }
  .card-back .brand { left: 103px; top: 110px; gap: 14px; }
  .card-back .brand-mark { width: 92px; height: 92px; background: var(--white); }
  .card-back .brand-name { color: var(--white); }
  .card-back .brand-name .line-main { font-size: 42px; }
  .card-back .brand-name .line-sub { font-size: 21px; }
</style>
</head>
<body>

  <section class="card card-front" aria-label="Business card front">
    <svg class="bands" width="588" height="363" viewBox="0 0 588 363">
      <polygon points="0,169 404,169 380,195 0,195" fill="var(--grey)"/>
      <polygon points="414,161 588,161 588,363 0,363 0,198 384,198" fill="var(--orange)"/>
    </svg>

    <div class="brand">
      <span class="brand-mark"></span>
      <div class="brand-name">
        <span class="line-main">Dig Line</span>
        <span class="line-sub">Contracting Inc</span>
      </div>
    </div>

    <div class="contact">
      <div class="contact-row">
        <span>(055)-321-6408</span>
        <svg width="11" height="11" viewBox="0 0 24 24" aria-hidden="true"><path fill="#fff" d="M6.6 10.8a15.2 15.2 0 0 0 6.6 6.6l2.2-2.2a1 1 0 0 1 1-.25 11.4 11.4 0 0 0 3.6.57 1 1 0 0 1 1 1V20a1 1 0 0 1-1 1A17 17 0 0 1 3 4a1 1 0 0 1 1-1h3.5a1 1 0 0 1 1 1c0 1.25.2 2.45.57 3.57a1 1 0 0 1-.25 1z"/></svg>
      </div>
      <div class="contact-row">
        <span>hello@yourmail.com</span>
        <svg width="12" height="9" viewBox="0 0 24 18" aria-hidden="true"><rect width="24" height="18" rx="1" fill="#fff"/><path d="M1 1l11 9 11-9" fill="none" stroke="var(--orange)" stroke-width="2"/></svg>
      </div>
    </div>

    <div class="person">
      <div class="person-name">Daniel Reyes</div>
      <div class="person-title">Managing Director</div>
    </div>

    <div class="address address-mailing">
      <div class="address-title">Mailing Address</div>
      <div>12345, Address Goes Here</div>
      <div>Country Name, 123456</div>
    </div>

    <div class="address address-shop">
      <div class="address-title">Shop Address</div>
      <div>12345, Address Goes Here</div>
      <div>Country Name, 123456</div>
    </div>
  </section>

  <section class="card card-back" aria-label="Business card back">
    <div class="brand">
      <span class="brand-mark"></span>
      <div class="brand-name">
        <span class="line-main">Dig Line</span>
        <span class="line-sub">Contracting Inc</span>
      </div>
    </div>
  </section>

</body>
</html>
```